Structural Engineering Business Card

Brookvane Drafting does residential house plans for clients in Central Florida. Would like simple but elegant business card that is appropriate for a house plan engineering company. Prefer black business card with black/white them but open to other shades of blue. I uploaded a sample card that I came across that looked good but please come up with your own creative designs.

Contact Information for Business Card

Name, Title, Phone, Email, Address, website

```html
<!DOCTYPE html>
<html lang="en">
<head>
<meta charset="utf-8">
<title>Brookvane Drafting – Business Card</title>
<link href="https://fonts.googleapis.com/css2?family=Montserrat:wght@400;500;700;800&display=swap" rel="stylesheet">
<style>
  :root {
    --page-bg: #b3b3b3;
    --card-bg: #262626;
    --accent: #56c3e4;
    --logo-grey: #8a8a8a;
    --text-light: #e6e6e6;
    --text-muted: #bdbdbd;
  }
  * { margin: 0; padding: 0; box-sizing: border-box; }
  html, body {
    width: 1200px; height: 900px; overflow: hidden;
    background: var(--page-bg);
    font-family: "Montserrat", Arial, sans-serif;
  }
  .sheet {
    width: 1200px; height: 900px;
    display: flex; flex-direction: column; align-items: center; justify-content: center;
    gap: 40px;
  }
  .card {
    position: relative;
    width: 680px; height: 390px;
    background: var(--card-bg);
    border-radius: 26px;
    border-bottom: 5px solid var(--accent);
    overflow: hidden;
  }

  /* Shared wordmark */
  .brand { display: flex; align-items: center; gap: 14px; white-space: nowrap; }
  .brand-dot {
    width: 26px; height: 26px; border-radius: 50%;
    background: var(--accent); flex: none;
  }
  .brand-name {
    font-weight: 800; font-size: 36px; letter-spacing: 1px;
    color: var(--logo-grey); text-transform: uppercase; line-height: 1;
  }

  /* Front */
  .front-brand { position: absolute; left: 48px; top: 52px; }
  .person { position: absolute; left: 48px; top: 124px; }
  .person-name {
    font-weight: 700; font-size: 28px; color: var(--accent); line-height: 1.1;
  }
  .person-title {
    font-weight: 400; font-size: 16px; color: var(--text-muted); margin-top: 6px;
  }
  .address {
    position: absolute; right: 44px; top: 140px; text-align: right;
    font-size: 17px; color: var(--text-light); line-height: 1.35;
    font-style: normal;
  }
  .divider {
    position: absolute; left: 0; right: 0; top: 210px;
    height: 1.5px; background: var(--accent);
  }
  .contacts { position: absolute; left: 48px; top: 236px; list-style: none; }
  .contacts li {
    display: flex; align-items: center; gap: 14px;
    font-size: 18px; color: var(--text-light); line-height: 1; margin-bottom: 15px;
  }
  .contacts svg { width: 18px; height: 18px; flex: none; }

  /* Back */
  .blueprint {
    position: absolute; left: 40px; top: 40px;
    width: 420px; height: 305px;
    background: radial-gradient(ellipse at 50% 55%, #3a3a3a 0%, #2c2c2c 55%, var(--card-bg) 100%);
    border-radius: 6px;
  }
  .back-brand-wrap {
    position: absolute; right: 48px; top: 0; bottom: 0;
    display: flex; align-items: center;
  }
  .back-brand {
    writing-mode: vertical-rl;
    transform: rotate(180deg);
    gap: 16px;
  }
  .back-brand .brand-name { font-size: 38px; line-height: 1.05; }
</style>
</head>
<body>
<main class="sheet">

  <section class="card card-front">
    <div class="brand front-brand">
      <span class="brand-dot"></span>
      <span class="brand-name">Brookvane Drafting</span>
    </div>

    <div class="person">
      <p class="person-name">Daniel Harper</p>
      <p class="person-title">Owner</p>
    </div>

    <address class="address">Lindenweg 42<br>20095 Hamburg</address>

    <div class="divider"></div>

    <ul class="contacts">
      <li>
        <svg viewBox="0 0 24 24" aria-hidden="true"><path fill="#56c3e4" d="M6.6 10.8a15.5 15.5 0 0 0 6.6 6.6l2.2-2.2c.3-.3.7-.4 1-.2 1.1.4 2.3.6 3.6.6.6 0 1 .4 1 1V20c0 .6-.4 1-1 1A17 17 0 0 1 3 4c0-.6.4-1 1-1h3.5c.6 0 1 .4 1 1 0 1.3.2 2.5.6 3.6.1.3 0 .7-.2 1z"/></svg>
        +49 404 555 0182
      </li>
      <li>
        <svg viewBox="0 0 24 24" aria-hidden="true"><rect x="2" y="5" width="20" height="14" rx="2" fill="#56c3e4"/><path d="M3 6l9 7 9-7" fill="none" stroke="#262626" stroke-width="1.8"/></svg>
        info@brookvane-drafting.com
      </li>
      <li>
        <svg viewBox="0 0 24 24" aria-hidden="true"><circle cx="12" cy="12" r="10" fill="#56c3e4"/><path d="M2 12h20M12 2c3 3 3 17 0 20M12 2c-3 3-3 17 0 20" fill="none" stroke="#262626" stroke-width="1.5"/></svg>
        www.brookvane-drafting.com
      </li>
    </ul>
  </section>

  <section class="card card-back">
    <div class="blueprint" role="img" aria-label="Line drawing of a two-storey house elevation with dimension lines"></div>
    <div class="back-brand-wrap">
      <div class="brand back-brand">
        <span class="brand-dot"></span>
        <span class="brand-name">Brookvane<br>Drafting</span>
      </div>
    </div>
  </section>

</main>
</body>
</html>
```